Coastline Premier Retreats Business Card Design

Design a business card for Coastline Premier Retreats. Look at the website for colors and reference. Card should have logo, name, title, office number, mobile number, email, URL and a tagline like, "Luxury Hotel & Resort Email Marketing" (This might change).

https://www.coastlinepremierretreats.example

The rest I will leave up to your imagination.

Contact Information for Business Card

Logo, name, title, office number, mobile number, email, URL and a tagline like, "Luxury Hotel & Resort Email Marketing" (This might change).

```html
<!DOCTYPE html>
<html lang="en">
<head>
<meta charset="utf-8">
<title>Coastline Premier Retreats – Business Card</title>
<link rel="stylesheet" href="https://fonts.googleapis.com/css2?family=Open+Sans:wght@400;600;700&display=swap">
<style>
  :root {
    --stage: #232323;
    --card-dark: #1e1e22;
    --card-facet: #25252a;
    --orange: #f37321;
    --orange-deep: #d8611a;
    --white: #ffffff;
    --muted: #e6e6e6;
  }
  * { box-sizing: border-box; margin: 0; padding: 0; }
  html, body {
    width: 1200px; height: 780px; overflow: hidden;
    background: var(--stage);
    font-family: "Open Sans", Arial, sans-serif;
  }
  .stage {
    width: 1200px; height: 780px;
    display: flex; align-items: center; justify-content: center; gap: 40px;
  }
  .card {
    position: relative;
    width: 540px; height: 309px;
    border-radius: 2px;
    overflow: hidden;
    box-shadow: 0 18px 40px rgba(0,0,0,.45);
  }
  /* Front */
  .card-front { background: var(--card-dark); }
  .card-front .facets { position: absolute; inset: 0; }
  .brand-name {
    position: absolute; left: 30px; top: 30px;
    color: var(--white);
    font-weight: 600; font-size: 19px; letter-spacing: .5px;
    text-transform: uppercase;
  }
  .info-column {
    position: absolute; right: 30px; top: 96px; bottom: 20px;
    display: flex; flex-direction: column; justify-content: flex-end;
    align-items: flex-end; gap: 12px;
    text-align: right;
  }
  .person-name { font-weight: 700; font-size: 26px; line-height: 1.15; color: var(--white); }
  .person-name .first { color: var(--orange); }
  .person-title { font-size: 13px; line-height: 1.4; color: var(--white); margin-top: 2px; }
  .tagline { font-size: 12.5px; color: var(--orange); line-height: 1.35; margin-top: 4px; }
  .contacts { list-style: none; }
  .contacts li {
    display: flex; align-items: center; justify-content: flex-end; gap: 9px;
    font-size: 12px; color: var(--muted); line-height: 1.5;
  }
  .contacts svg { width: 13px; height: 13px; flex: none; }
  /* Back */
  .card-back {
    background: var(--orange);
    display: flex; align-items: center; justify-content: center;
  }
  .back-brand {
    color: var(--orange-deep);
    font-weight: 700; font-size: 30px; letter-spacing: 1px;
    text-transform: uppercase; text-align: center; line-height: 1.2;
  }
</style>
</head>
<body>
<main class="stage">
  <section class="card card-front" aria-label="Business card front">
    <svg class="facets" viewBox="0 0 540 309" preserveAspectRatio="none" aria-hidden="true">
      <polygon points="0,0 540,0 540,250 20,130 0,130" fill="var(--card-facet)"/>
      <polygon points="20,130 540,250 540,309 0,309 0,130" fill="var(--card-dark)"/>
    </svg>
    <div class="brand-name">Coastline Premier Retreats</div>

    <div class="info-column">
      <div class="person">
        <h1 class="person-name"><span class="first">Marta</span> Kovalenko</h1>
        <p class="person-title">Co-Founder</p>
        <p class="tagline">Luxury Hotel &amp;<br>Resort Email Marketing</p>
      </div>

      <ul class="contacts">
        <li>(555) 014-2758
          <svg viewBox="0 0 16 16" aria-hidden="true"><path fill="var(--orange)" d="M3.6 1.5l2.3 2.8-1.4 1.6c.9 2 2.5 3.6 4.6 4.6l1.6-1.4 2.8 2.3-1.3 2.1C7.4 13.3 2.7 8.6 1.5 3.2z"/></svg>
        </li>
        <li>(555) 019-7777
          <svg viewBox="0 0 16 16" aria-hidden="true"><rect x="4" y="1" width="8" height="14" rx="1.5" fill="none" stroke="var(--orange)" stroke-width="1.5"/><circle cx="8" cy="12.5" r=".9" fill="var(--orange)"/></svg>
        </li>
        <li>www.coastlinepremierretreats.example
          <svg viewBox="0 0 16 16" aria-hidden="true"><circle cx="8" cy="8" r="6.5" fill="none" stroke="var(--orange)" stroke-width="1.4"/><path d="M1.5 8h13M8 1.5c2.2 2 2.2 11 0 13M8 1.5c-2.2 2-2.2 11 0 13" fill="none" stroke="var(--orange)" stroke-width="1.1"/></svg>
        </li>
        <li>info@coastlinepremierretreats.example
          <svg viewBox="0 0 16 16" aria-hidden="true"><rect x="1.5" y="3.5" width="13" height="9" rx="1" fill="var(--orange)"/><path d="M1.8 4l6.2 5 6.2-5" fill="none" stroke="var(--card-dark)" stroke-width="1.2"/></svg>
        </li>
      </ul>
    </div>
  </section>

  <section class="card card-back" aria-label="Business card back">
    <div class="back-brand">Coastline<br>Premier Retreats</div>
  </section>
</main>
</body>
</html>
```